Hardcore nerd needs to stand out in a sea of dull Defence business cards

Wombarra Devices is a new Australian consulting engineering company that turns research and theory into practical systems. No evangelistic fluff, just mathematics and physics into electronic and optical circuits for consumer products, scientific research or Defence applications.

We already have a recognised logo (provided) which is often dark blue/black on a light background but we're open to other combinations. (Us engineers tend to have limited aesthetic imagination :)

Some of our recent products have included:
* Instrumentation for electrical testing,
* Radar jammers,
* GPS antenna design,
* Satellite tracking systems,
* High power lasers

We're open to both single and double-sided designs - happy to be convinced either way.

P.S. Another group is working on the web page, so - alas - our web site is currently of no use for images/ideas...

Target Market(s)

Engineering managers,
Scientists

Contact Information for Business Card

Dr Colin Harte
R&D Engineer

colin@wombarradevices.com.au
0427 563 710

PO Box XXX (to be confirmed)
Kelsby ACT 2917
Australia

Font styles to use
Serif
Sans Serif

Colors

Designer to choose colors to be used in the design.

Requirements
Must have
• My contact details!
• I've had many (great) "bold and plain" designs submitted already, so feel free to be artistically creative :)
• Happy to take advice re fonts/colours/printability etc.
Nice to have
• I'm not sure if "lists" are more at home on a CV than a business card, but representative services include:
• Applied electromagnetics
• RF and high speed electronics
• Signal and image processing
• Electro-optical and laser systems
• Concept-to-prototype design services
• If you're considering double sided cards, then often measuring/alignment grids/rulers feature on the back of similar cards.
• e.g. https://www.veltranoptics.example/newgrouppage9.cfm?objectgroup_id=4183
• https://www.veltranoptics.example/newgrouppage9.cfm?objectgroup_ID=4185
• ..or even a "Smith chart" (google will return lots)
• Generic images to represent a capability might work - googling images associated with keyword for each of these areas might help:
• - "passive radar", "phased array", "fdtd", "vircator"
• RF and high speed electronic design
• - "smith chart", "microstrip circuits", "dimensioned drawing", "electronic schematic"
• - "dft", "iir filter"
• - "optical cavity". "laser energy level diagram"
• Background/watermarked images outlines/wireframes/schematics would probably look OK.
Should not have
• If a list of projects/services is provided, it is important not to make the client feel that this is "all" the company can do. Engineering design is a creative discipline (like graphics :)
• Please, no stock "military" snaps like planes, missiles, etc!

```html
<!DOCTYPE html>
<html lang="en">
<head>
<meta charset="utf-8">
<title>Wombarra Devices – Business Card</title>
<link href="https://fonts.googleapis.com/css2?family=Arimo:wght@700&family=Lato:wght@400&family=PT+Sans:wght@400;700&display=swap" rel="stylesheet">
<style>
  :root {
    --backdrop: #4f4f4f;
    --paper: #ffffff;
    --navy: #0c1f5f;
    --ink: #2b2b2b;
    --shadow: rgba(0, 0, 0, 0.45);
  }
  * { margin: 0; padding: 0; box-sizing: border-box; }
  html, body { width: 1200px; height: 900px; overflow: hidden; }
  body { background: var(--backdrop); position: relative; font-family: "Lato", Arial, sans-serif; }

  .card {
    position: absolute;
    top: 200px;
    width: 310px;
    height: 502px;
    box-shadow: 4px 4px 6px var(--shadow);
  }
  .card--front {
    left: 253px;
    background: var(--paper);
    border-radius: 72px 0 72px 0;
  }
  .card--back {
    left: 627px;
    background: var(--navy);
    border-radius: 0 72px 0 72px;
  }

  /* Front: brand lockup */
  .brand {
    position: absolute;
    left: 27px;
    top: 100px;
    display: flex;
    align-items: center;
    gap: 8px;
    color: var(--navy);
    font-family: "PT Sans", Arial, sans-serif;
    font-weight: 700;
  }
  .brand__dot {
    width: 88px; height: 88px;
    border-radius: 50%;
    background: var(--navy);
    flex: none;
  }
  .brand__name { line-height: 1; }
  .brand__line1 { display: block; font-size: 29px; letter-spacing: 0.5px; }
  .brand__line2 { display: block; font-size: 17px; letter-spacing: 3.6px; margin-top: 4px; }

  /* Front: contact block */
  .person {
    position: absolute;
    left: 33px;
    top: 311px;
  }
  .person__name {
    font-family: "Arimo", Arial, sans-serif;
    font-weight: 700;
    font-size: 17.5px;
    color: var(--navy);
    letter-spacing: 0.2px;
    line-height: 20px;
  }
  .person__role { font-size: 14px; color: var(--ink); line-height: 17px; }

  .contact-list {
    list-style: none;
    margin-top: 12px;
    font-size: 14px;
    color: var(--ink);
  }
  .contact-list li {
    display: flex;
    align-items: center;
    gap: 5px;
    height: 18.5px;
  }
  .contact-list svg { width: 12px; height: 12px; fill: var(--navy); flex: none; }

  .address {
    margin-top: 10px;
    font-style: normal;
    font-size: 14px;
    line-height: 18.5px;
    color: var(--ink);
  }

  /* Back */
  .back-brand {
    position: absolute;
    left: 0; right: 0;
    top: 117px;
    display: flex;
    flex-direction: column;
    align-items: center;
    gap: 14px;
    color: var(--paper);
    font-family: "PT Sans", Arial, sans-serif;
    font-weight: 700;
  }
  .back-brand__dot {
    width: 118px; height: 118px;
    border-radius: 50%;
    background: var(--paper);
  }
  .back-brand__name { font-size: 24px; letter-spacing: 1.5px; }

  .services {
    position: absolute;
    left: 30px;
    top: 361px;
    list-style: none;
    font-family: "PT Sans", Arial, sans-serif;
    font-size: 16px;
    color: var(--paper);
  }
  .services li {
    display: flex;
    align-items: center;
    gap: 6px;
    height: 22.7px;
  }
  .services li::before {
    content: "";
    width: 10px; height: 10px;
    border-radius: 50%;
    background: var(--paper);
    flex: none;
  }
</style>
</head>
<body>

  <section class="card card--front" aria-label="Business card front">
    <div class="brand">
      <span class="brand__dot" aria-hidden="true"></span>
      <span class="brand__name">
        <span class="brand__line1">WOMBARRA</span>
        <span class="brand__line2">DEVICES</span>
      </span>
    </div>

    <div class="person">
      <h1 class="person__name">DR COLIN HARTE</h1>
      <p class="person__role">R&amp;D Engineer</p>

      <ul class="contact-list">
        <li>
          <svg viewBox="0 0 12 12" aria-hidden="true"><path d="M1 4.2C1 3 3 2 6 2s5 1 5 2.2v1H8.4V4.1H3.6v1.1H1zM3 6h6l1.6 4H1.4z"/></svg>
          0427 563 710
        </li>
        <li>
          <svg viewBox="0 0 12 12" aria-hidden="true"><path d="M1 2.5h10v7H1zM1.8 3.4L6 6.6l4.2-3.2" stroke="#fff" stroke-width="0.9"/></svg>
          colin@wombarradevices.com.au
        </li>
        <li>
          <svg viewBox="0 0 12 12" aria-hidden="true"><circle cx="6" cy="6" r="5.2"/><path d="M1 6h10M6 .8c-2.2 2.8-2.2 7.6 0 10.4M6 .8c2.2 2.8 2.2 7.6 0 10.4" stroke="#fff" stroke-width="0.8" fill="none"/></svg>
          www.wombarradevices.com.au
        </li>
      </ul>

      <address class="address">
        PO Box XXX<br>
        Kelsby ACT 2917, Australia
      </address>
    </div>
  </section>

  <section class="card card--back" aria-label="Business card back">
    <div class="back-brand">
      <span class="back-brand__dot" aria-hidden="true"></span>
      <span class="back-brand__name">WOMBARRA DEVICES</span>
    </div>

    <ul class="services">
      <li>Applied electromagnetics</li>
      <li>RF and high speed electronics</li>
      <li>Signal and image processing</li>
      <li>Electro-optical and laser systems</li>
    </ul>
  </section>

</body>
</html>
```